Harborline Renewal Business Card Design

Professional and clean design. The design colors should flow with the logo. Two-sided card with the website on the back which is:

www.HarborlineRenewal.example.

"Specializing in Water Damage Restoration"

On the front I need the name, email, phone, and logo.

Name: Darnell Quisby
Email: Darnell@HarborlineRenewal.example
Phone: 555-318-2046 for now

I only have the Preview and Thumbnail right now but should have the source files uploaded within a day or two.

Target Market(s)

Flood victims, home owners with water damage from busted pipes etc...

Industry/Entity Type

Business

Contact Information for Business Card

Name: Darnell Quisby

Font styles to use
Serif
Sans Serif

Requirements
Must have
• Business Card Details Info

```html
<!DOCTYPE html>
<html lang="en">
<head>
<meta charset="utf-8">
<title>Harborline Renewal Business Card</title>
<link rel="stylesheet" href="https://fonts.googleapis.com/css2?family=Open+Sans:wght@400;600;700&display=swap">
<style>
  :root {
    --page: #e9e6e1;
    --card-black: #0b0b0c;
    --card-black-soft: #1a1a1c;
    --brand-blue: #2a9ad8;
    --swoosh-grey: #d9d9d9;
    --text-white: #f2f2f2;
  }
  * { box-sizing: border-box; margin: 0; padding: 0; }
  html, body { width: 1200px; height: 900px; overflow: hidden; }
  body {
    background: var(--page);
    font-family: "Open Sans", Arial, sans-serif;
    position: relative;
  }
  .card {
    position: absolute;
    width: 600px;
    height: 343px;
    background: radial-gradient(ellipse at 50% 35%, var(--card-black-soft), var(--card-black) 75%);
    border-radius: 4px;
    box-shadow: 0 10px 30px rgba(0,0,0,0.25);
    overflow: hidden;
  }
  .card-back { left: 50px; top: 90px; }
  .card-front { left: 550px; top: 470px; }

  .back-wordmark {
    position: absolute;
    top: 118px; left: 0; right: 0;
    text-align: center;
    color: var(--text-white);
    font-weight: 600;
    font-size: 34px;
    letter-spacing: 3px;
    text-transform: uppercase;
  }
  .tagline {
    position: absolute;
    top: 250px; left: 0; right: 0;
    text-align: center;
    color: var(--brand-blue);
    font-size: 19px;
  }

  .front-art { position: absolute; inset: 0; width: 100%; height: 100%; }
  .front-brand {
    position: absolute;
    top: 36px; right: 34px;
    display: flex; flex-direction: column; align-items: center; gap: 8px;
  }
  .brand-dot {
    width: 40px; height: 40px; border-radius: 50%;
    background: var(--brand-blue);
  }
  .front-wordmark {
    color: var(--brand-blue);
    font-weight: 600;
    font-size: 20px;
    letter-spacing: 2px;
    text-transform: uppercase;
  }
  .person-name {
    position: absolute;
    top: 56px; left: 44px;
    color: var(--brand-blue);
    font-weight: 700;
    font-size: 20px;
  }
  .address {
    position: absolute;
    top: 125px; left: 44px;
    color: var(--text-white);
    font-size: 15px;
    line-height: 1.4;
  }
  .contact {
    position: absolute;
    top: 195px; left: 44px;
    list-style: none;
    color: var(--text-white);
    font-size: 15px;
    line-height: 1.45;
  }
  .contact li { display: flex; align-items: center; gap: 9px; }
  .contact svg { width: 12px; height: 12px; fill: var(--brand-blue); }
  .website {
    position: absolute;
    right: 24px; bottom: 50px;
    color: var(--text-white);
    font-size: 14px;
  }
</style>
</head>
<body>
  <section class="card card-back" aria-label="Card back">
    <div class="back-wordmark">Harborline Renewal</div>
    <p class="tagline">Specializing in Water Damage Restoration</p>
  </section>

  <section class="card card-front" aria-label="Card front">
    <svg class="front-art" viewBox="0 0 600 343" preserveAspectRatio="none" aria-hidden="true">
      <path d="M0 305 C160 305 280 285 370 245 C450 208 520 160 600 128 L600 343 L0 343 Z" fill="var(--swoosh-grey)"/>
      <path d="M0 320 C160 320 285 300 375 260 C455 222 525 172 600 140 L600 343 L0 343 Z" fill="var(--brand-blue)"/>
    </svg>
    <div class="front-brand">
      <span class="brand-dot"></span>
      <span class="front-wordmark">Harborline Renewal</span>
    </div>
    <h1 class="person-name">Darnell Quisby</h1>
    <p class="address">1234, Address GoesHere,<br>Country, 12345</p>
    <ul class="contact">
      <li><svg viewBox="0 0 12 12"><rect x="3" y="0" width="6" height="12" rx="1.2"/></svg>555-318-2046</li>
      <li><svg viewBox="0 0 12 12"><path d="M0 2h12v8H0z"/></svg>Darnell@HarborlineRenewal.example</li>
    </ul>
    <p class="website">www.HarborlineRenewal.example</p>
  </section>
</body>
</html>
```